Simple and Clean business card design

We would like the design to be simple clean and to incorporate our colors.

We are open to your design and talent, we have the dots in our logo as we think of it as data points and we connect data points for people.

We are open to see the great creative and clean design you bring to the table

Contact Information for Business Card

please include: name, position, email, phone and website

Font styles to use
Sans Serif

Requirements
Must have
• my colors incorporated, simplicity
Nice to have
• lots of white space, simplicity
Should not have
• complexicity/ complex art

```html
<!DOCTYPE html>
<html lang="en">
<head>
<meta charset="utf-8">
<title>Sorrel Business Card</title>
<link rel="stylesheet" href="https://fonts.googleapis.com/css2?family=Montserrat:wght@600;700&family=Work+Sans:wght@400;600&display=swap">
<style>
  :root {
    --stage: #d9dadc;
    --card: #050505;
    --card-edge: #161616;
    --white: #ffffff;
    --blue: #5b84c9;
    --green: #3fae5a;
    --yellow: #f3c01f;
    --red: #e4483b;
    --muted: #e8e8e8;
  }
  * { box-sizing: border-box; margin: 0; padding: 0; }
  html, body {
    width: 1200px; height: 913px; overflow: hidden;
    background: var(--stage);
  }
  .stage {
    width: 1200px; height: 913px;
    display: flex; flex-direction: column;
    align-items: center; justify-content: center; gap: 36px;
  }
  .card {
    position: relative;
    width: 700px; height: 400px;
    background: var(--card);
    border-radius: 14px;
    box-shadow: 0 10px 30px rgba(0,0,0,.25);
    overflow: hidden;
    color: var(--white);
  }
  .wordmark {
    display: flex; align-items: center; gap: 14px;
    font-family: "Work Sans", sans-serif;
    font-weight: 600;
    color: var(--white);
    letter-spacing: -1px;
  }
  .wordmark-dot {
    width: 22px; height: 22px; border-radius: 50%;
    background: var(--blue);
  }
  .card-front .wordmark {
    position: absolute; left: 50%; top: 50%;
    transform: translate(-50%, -50%);
    font-size: 104px;
  }
  .card-back .wordmark {
    position: absolute; left: 70px; top: 210px;
    font-size: 78px;
  }
  .divider {
    position: absolute; left: 395px; top: 70px;
    width: 2px; height: 260px;
    background: var(--blue);
  }
  .contact {
    position: absolute; left: 425px; top: 78px;
    font-family: "Work Sans", sans-serif;
    font-size: 15px; line-height: 1.45;
    color: var(--muted);
  }
  .contact-name {
    font-family: "Montserrat", sans-serif;
    font-weight: 700; font-size: 22px;
    color: var(--blue); letter-spacing: .5px;
    line-height: 1.1;
  }
  .contact-role { font-size: 16px; margin-bottom: 14px; }
  .contact-address { margin-bottom: 14px; }
  .contact-line { display: flex; align-items: center; gap: 8px; }
  .contact-line svg { width: 12px; height: 12px; flex: none; }
</style>
</head>
<body>
<main class="stage">
  <section class="card card-front" aria-label="Card front">
    <div class="wordmark"><span class="wordmark-dot"></span>Sorrel</div>
  </section>

  <section class="card card-back" aria-label="Card back">
    <div class="wordmark"><span class="wordmark-dot"></span>Sorrel</div>
    <div class="divider"></div>
    <div class="contact">
      <p class="contact-name">DANIEL ROWE</p>
      <p class="contact-role">Founder</p>
      <p class="contact-address">418 Birchwood Lane<br>Brookfield, TX 75001</p>
      <p class="contact-line">
        <svg viewBox="0 0 12 12" aria-hidden="true"><path d="M3 1 L5 3.5 L4 5 Q5.5 7.5 7 8 L8.5 7 L11 9 L9.5 11 Q4 10.5 1 3 Z" fill="var(--blue)"/></svg>
        0412 555 019
      </p>
      <p class="contact-line">
        <svg viewBox="0 0 12 12" aria-hidden="true"><rect x="1" y="2.5" width="10" height="7" fill="none" stroke="var(--blue)" stroke-width="1.2"/><path d="M1 2.5 L6 6.5 L11 2.5" fill="none" stroke="var(--blue)" stroke-width="1.2"/></svg>
        info@northfieldgrid.com
      </p>
      <p class="contact-line">
        <svg viewBox="0 0 12 12" aria-hidden="true"><circle cx="6" cy="6" r="5" fill="none" stroke="var(--blue)" stroke-width="1.1"/><ellipse cx="6" cy="6" rx="2.2" ry="5" fill="none" stroke="var(--blue)" stroke-width="1"/><path d="M1 6 H11" stroke="var(--blue)" stroke-width="1"/></svg>
        www.northfieldgrid.com
      </p>
    </div>
  </section>
</main>
</body>
</html>
```